Wine Label Design

A wine label for 750ml bottles. Same label for different varieties with the variety / region / vintage to be updated as required.
Brand: Beyond the Ridge
Product Use: Front and Back label suitable for a 750 ml bottle (preferably Burgundy bottles)
Design Brief: Beyond the Ridge is a small winery that produces limited amounts of hand crafted wines that are aimed at the mid to top end of the market and requires a label befitting the work that goes into the creation of the wine. In terms of style i don't have any preconceptions and am open to a broad range of design suggestions at the same level of existing premium brands or innovative brands.
Must Have for Front label
Front Label
Beyond the Ridge
2013
Grampians
Shiraz
750ML (should be in smaller text)
Alc. 14% by Vol. (should be in smaller text)
Must Have for Back Label
Beyond the Ridge
2013
Grampians
Shiraz
www.beyondtheridge.com.au (should be in smaller text)
Product of Australia
Alc.14% by Vol. (should be in smaller text)
Contains preservative 220(should be in smaller text)
Below are some guides for dimensions:
The Front Label Size can be between
100 - 120 mm (Width) x 70 - 85 mm (Height)
The back label size can be between
90 mm (Width) x 70 - 85 mm (Height)
Updates
Target Market(s)
Medium to top end of the wine market who require the label to be a reflection of the wine.
Industry/Entity Type
Product
Colors
Designer to choose colors to be used in the design.
Look and feel
Each slider illustrates characteristics of the customer's brand and the style your logo design should communicate.

```html
<!DOCTYPE html>
<html lang="en">
<head>
<meta charset="utf-8">
<title>Beyond the Ridge — Grampians Shiraz 2013</title>
<link rel="stylesheet" href="https://fonts.googleapis.com/css2?family=Source+Sans+3:wght@400&display=swap">
<style>
  :root {
    --label-charcoal: #373634;
    --text-white: #ffffff;
    --tone-orange: #e87722;
    --tone-green: #00693e;
    --tone-plum: #8e547a;
    --tone-olive: #6a8f2f;
  }
  html, body {
    margin: 0;
    padding: 0;
    width: 1200px;
    height: 1084px;
    overflow: hidden;
    background: var(--label-charcoal);
  }
  .wine-label {
    display: block;
    width: 1200px;
    height: 1084px;
  }
  .label-ground { fill: var(--label-charcoal); }
  .artwork-stop-orange { stop-color: var(--tone-orange); }
  .artwork-stop-green { stop-color: var(--tone-green); }
  .artwork-stop-plum { stop-color: var(--tone-plum); }
  .artwork-stop-olive { stop-color: var(--tone-olive); }
  .label-text {
    fill: var(--text-white);
    font-family: "Source Sans 3", "Myriad Pro", Arial, sans-serif;
    font-weight: 400;
  }
  .brand-name { font-size: 60px; }
  .wine-detail { font-size: 39px; }
  .origin { font-size: 51px; }
  .legal { font-size: 35px; }
  .web-address { font-size: 39px; }
</style>
</head>
<body>
<svg class="wine-label" viewBox="0 0 1200 1084" xmlns="http://www.w3.org/2000/svg" role="group" aria-label="Beyond the Ridge Grampians Shiraz 2013 label">
  <defs>
    <linearGradient id="artwork-tones" x1="0" y1="0" x2="0" y2="1">
      <stop class="artwork-stop-orange" offset="0"/>
      <stop class="artwork-stop-green" offset="0.4"/>
      <stop class="artwork-stop-plum" offset="0.65"/>
      <stop class="artwork-stop-olive" offset="1"/>
    </linearGradient>
  </defs>

  <rect class="label-ground" x="0" y="0" width="1200" height="1084"/>

  <rect class="artwork-area" x="0" y="574" width="468" height="510" fill="url(#artwork-tones)"
        role="img" aria-label="Artwork of layered rolling hills in orange, green, plum and olive"/>

  <g class="label-text">
    <text class="brand-name" x="686" y="147">BEYOND THE RIDGE</text>
    <text class="wine-detail region" x="687" y="236">Grampians</text>
    <text class="wine-detail variety" x="687" y="285">Shiraz</text>
    <text class="wine-detail vintage" x="687" y="377">2013</text>

    <text class="origin" x="688" y="758">Product of Australia</text>
    <text class="legal volume" x="693" y="864">750ML</text>
    <text class="legal alcohol" x="693" y="910">Alc.14% by Vol.</text>
    <text class="legal preservative" x="693" y="956">Contains preservative 220</text>
    <text class="web-address" x="692" y="1024">www.beyondtheridge.com.au</text>
  </g>
</svg>
</body>
</html>
```